Harbor Ledger Funds Bus card and Logo

I need a logo design and Bus card design. The fund focuses on evaluating and investing in minerals (sub-surface rights) and real estate.

Harbor ledger refers to a book of knowledge that each plebe gets when entering the Kelmont Marine Academy (my alma mater)

Target Market(s)

Investors and financial advisors

Contact Information for Business Card

Simple - perhaps a logo with a theme on book of knowledge

Logo Text

Ex Scientia Imperium

Font styles to use
Serif
Sans Serif

Colors

Designer to choose colors to be used in the design.

Requirements
Must have
• memorable logo that is relatively simple

```html
<!DOCTYPE html>
<html lang="en">
<head>
<meta charset="utf-8">
<title>Harbor Ledger Funds – Business Card</title>
<link rel="stylesheet" href="https://fonts.googleapis.com/css2?family=Montserrat:wght@600&family=Roboto:wght@500&family=Work+Sans:wght@400&display=swap">
<style>
  :root {
    --backdrop: #1f1f21;
    --paper: #ffffff;
    --navy: #143a6b;
    --sky: #00aeef;
    --ink: #1d3a63;
  }
  * { margin: 0; padding: 0; box-sizing: border-box; }
  html, body { width: 1200px; height: 900px; overflow: hidden; background: var(--backdrop); }
  .stage { position: relative; width: 1200px; height: 900px; }

  .card { position: absolute; left: 297px; width: 607px; height: 346px; overflow: hidden; }
  .card-front { top: 89px; background: var(--paper); }
  .card-back { top: 465px; background: var(--navy); }

  .card-wave { position: absolute; left: 0; top: 0; width: 607px; height: 346px; }

  .brand { position: absolute; display: flex; align-items: center; gap: 10px; }
  .brand-mark { flex: none; background: var(--sky); }
  .brand-name {
    font-family: "Montserrat", sans-serif; font-weight: 600;
    line-height: 1.15; letter-spacing: 0.5px;
  }

  .card-front .brand { left: 38px; top: 150px; width: 250px; }
  .card-front .brand-mark { width: 22px; height: 22px; }
  .card-front .brand-name { color: var(--navy); font-size: 21px; }

  .divider { position: absolute; left: 311px; top: 92px; width: 1.5px; height: 162px; background: var(--navy); }

  .contact { position: absolute; left: 343px; top: 84px; font-family: "Work Sans", sans-serif; color: var(--ink); }
  .contact-name { font-family: "Roboto", sans-serif; font-weight: 500; font-size: 29px; color: var(--sky); line-height: 1.1; letter-spacing: 0.3px; }
  .contact-role { font-size: 15px; margin-top: 2px; }
  .contact-address { font-size: 15px; line-height: 20px; margin-top: 12px; }
  .contact-lines { list-style: none; font-size: 15px; line-height: 20px; margin-top: 10px; }
  .contact-lines li { display: flex; align-items: center; gap: 8px; }
  .contact-lines svg { width: 9px; height: 9px; flex: none; }

  .card-back .brand { left: 60px; top: 40px; align-items: flex-end; gap: 40px; }
  .card-back .brand-mark { width: 200px; height: 200px; border-radius: 18px; }
  .card-back .brand-name { color: var(--paper); font-size: 30px; padding-bottom: 2px; }
</style>
</head>
<body>
<main class="stage">

  <section class="card card-front" aria-label="Business card front">
    <svg class="card-wave" viewBox="0 0 607 346" aria-hidden="true">
      <path d="M0 274 C150 318 360 338 607 304 L607 346 L0 346 Z" fill="var(--navy)"/>
      <path d="M95 298 C250 326 450 322 607 288 L607 297 C450 328 250 334 95 298 Z" fill="var(--sky)"/>
      <path d="M110 306 C260 336 460 332 607 303" fill="none" stroke="var(--paper)" stroke-width="2"/>
    </svg>

    <div class="brand">
      <span class="brand-mark"></span>
      <span class="brand-name">HARBOR LEDGER<br>FUNDS LLC</span>
    </div>

    <div class="divider"></div>

    <div class="contact">
      <h1 class="contact-name">DANIEL BROOKS</h1>
      <p class="contact-role">Director</p>
      <p class="contact-address">418 Cedar Hollow Lane<br>Maple Ridge, CA 95710</p>
      <ul class="contact-lines">
        <li>
          <svg viewBox="0 0 10 10" aria-hidden="true"><path d="M2 1 L4 1 L4.6 3.2 L3.4 4 C3.9 5.3 4.7 6.1 6 6.6 L6.8 5.4 L9 6 L9 8 C9 8.6 8.6 9 8 9 C4.5 9 1 5.5 1 2 C1 1.4 1.4 1 2 1 Z" fill="var(--sky)"/></svg>
          +330 5170-4426
        </li>
        <li>
          <svg viewBox="0 0 10 10" aria-hidden="true"><rect x="0.8" y="2" width="8.4" height="6" fill="none" stroke="var(--sky)" stroke-width="1"/><path d="M0.8 2 L5 5.5 L9.2 2" fill="none" stroke="var(--sky)" stroke-width="1"/></svg>
          info@harborledgerfunds.com
        </li>
        <li>
          <svg viewBox="0 0 10 10" aria-hidden="true"><circle cx="5" cy="5" r="4.2" fill="none" stroke="var(--sky)" stroke-width="0.9"/><ellipse cx="5" cy="5" rx="1.8" ry="4.2" fill="none" stroke="var(--sky)" stroke-width="0.9"/><path d="M0.8 5 H9.2" stroke="var(--sky)" stroke-width="0.9"/></svg>
          www.harborledgerfunds.com
        </li>
      </ul>
    </div>
  </section>

  <section class="card card-back" aria-label="Business card back">
    <div class="brand">
      <span class="brand-mark"></span>
      <span class="brand-name">HARBOR LEDGER<br>FUNDS LLC</span>
    </div>
  </section>

</main>
</body>
</html>
```